Professional Package for CPA Firm

We would like a stationery design for our new CPA Firm based in Atlanta, GA called 'Vale 8'. We work with investors to help grow investments, tax free. We would like the design to have a professional/minimal look with a 'wow' factor. We need 9.5″ x 4.125″, 9x12, and 10x13 mailing envelopes, business cards, and a letterhead. We have a logo that is already complete. For the letterhead, we would like to have space to put credentials at the bottom of the page

Industry/Entity Type

CPA, Accounting

```html
<!DOCTYPE html>
<html lang="en">
<head>
<meta charset="utf-8">
<title>Vale 8 Business Cards</title>
<link href="https://fonts.googleapis.com/css2?family=Lato:wght@400;700&display=swap" rel="stylesheet">
<style>
  :root {
    --backdrop: #8c8c8c;
    --card-navy: #032b3f;
    --card-edge: #1ba4b6;
    --accent-teal: #1fa9bd;
    --text-light: #eef2f4;
    --divider: #c9d3d8;
  }
  * { box-sizing: border-box; margin: 0; padding: 0; }
  html, body {
    width: 1200px;
    height: 800px;
    overflow: hidden;
  }
  body {
    background: var(--backdrop);
    font-family: "Lato", sans-serif;
    position: relative;
  }
  .card {
    position: absolute;
    top: 246px;
    width: 540px;
    height: 308px;
    background: var(--card-navy);
    border: 2px solid var(--card-edge);
  }
  .card--contact { left: 45px; }
  .card--brand { left: 615px; }

  .identity {
    position: absolute;
    right: 262px;
    top: 108px;
    text-align: right;
    color: var(--text-light);
    font-size: 15px;
    line-height: 1.3;
  }
  .identity__name {
    color: var(--accent-teal);
    font-size: 21px;
    font-weight: 400;
    letter-spacing: 0.5px;
    text-transform: uppercase;
    margin-bottom: 4px;
  }
  .identity__role { margin-bottom: 4px; }

  .card__divider {
    position: absolute;
    left: 292px;
    top: 104px;
    width: 1px;
    height: 100px;
    background: var(--divider);
  }

  .contact-list {
    position: absolute;
    left: 308px;
    top: 112px;
    list-style: none;
    color: var(--text-light);
    font-size: 15px;
  }
  .contact-list__item {
    display: flex;
    align-items: center;
    gap: 9px;
    height: 21px;
  }
  .contact-list__icon {
    width: 12px;
    height: 12px;
    flex: none;
  }

  .brand-name {
    position: absolute;
    left: 0;
    right: 0;
    top: 50%;
    transform: translateY(-50%);
    text-align: center;
    color: var(--text-light);
    font-size: 64px;
    font-weight: 700;
    letter-spacing: 3px;
  }
</style>
</head>
<body>

  <section class="card card--contact" aria-label="Business card, contact side">
    <div class="identity">
      <p class="identity__name">Daniel Reyes</p>
      <p class="identity__role">President</p>
      <p class="identity__street">4120 Birchwood Road</p>
      <p class="identity__city">Marietta, Georgia 30062</p>
    </div>

    <div class="card__divider"></div>

    <ul class="contact-list">
      <li class="contact-list__item">
        <svg class="contact-list__icon" viewBox="0 0 12 12" aria-hidden="true">
          <path d="M2.5 1 L4.5 1 L5 3.5 L3.8 4.5 Q5 7 7.5 8.2 L8.5 7 L11 7.5 L11 9.5 Q10.5 11 9 11 Q1 10 1 2.5 Q1 1 2.5 1 Z" fill="var(--accent-teal)"/>
        </svg>
        <span>555-210-4471</span>
      </li>
      <li class="contact-list__item">
        <svg class="contact-list__icon" viewBox="0 0 12 12" aria-hidden="true">
          <rect x="1.5" y="2.5" width="9" height="7" fill="none" stroke="var(--accent-teal)" stroke-width="1.4"/>
        </svg>
        <span>555-210-4472</span>
      </li>
      <li class="contact-list__item">
        <svg class="contact-list__icon" viewBox="0 0 12 12" aria-hidden="true">
          <rect x="1" y="2.5" width="10" height="7.5" fill="var(--accent-teal)"/>
          <path d="M1.5 3 L6 6.8 L10.5 3" fill="none" stroke="var(--card-navy)" stroke-width="1.1"/>
        </svg>
        <span>info@vale8.com</span>
      </li>
      <li class="contact-list__item">
        <svg class="contact-list__icon" viewBox="0 0 12 12" aria-hidden="true">
          <circle cx="6" cy="6" r="5" fill="var(--accent-teal)"/>
          <path d="M1 6 H11 M6 1 Q3 6 6 11 M6 1 Q9 6 6 11" fill="none" stroke="var(--card-navy)" stroke-width="0.9"/>
        </svg>
        <span>www.vale8.com</span>
      </li>
    </ul>
  </section>

  <section class="card card--brand" aria-label="Business card, brand side">
    <p class="brand-name">Vale 8</p>
  </section>

</body>
</html>
```